NEW Modern Sleek Business Card for VR Language Startup

Our startup is using VR to lead the next wave of world language education. We need a two-sided business card that introduces the larger organization (Brightloom Language Inc) and our contact info on one side and shows the product, Glimwoorld, on the other side.

Side 1 (contact info)= Brightloom Logo and Contact info (name, title, phone, email)

Side 2 (product)= Glimworld logo, text, and website
Text= Culturally Immersive Language Learning Games
Website= www.glimworld-play.com

Target Market(s)

Education, Technology

Contact Information for Business Card

Contact info will be updated upon approval of the design. For now, put this as a placeholder.

Perry Dunmore
Founder & CEO
pdunmore@quillpost-mail.net
(555)-014-2286

Font styles to use
Other font styles liked:
• Gibson and Century Gothic are the brand fonts

Requirements
Nice to have
• I would love to see cohesion between the design and colors of the two logos. I have attached a few business card designs that I like, so you can get a feel for my preferred style.

```html
<!DOCTYPE html>
<html lang="en">
<head>
<meta charset="utf-8">
<title>Glimworld / Brightloom Language – Business Card</title>
<link href="https://fonts.googleapis.com/css2?family=Poppins:wght@400;500;600;700&display=swap" rel="stylesheet">
<style>
  :root {
    --backdrop: #9a9a9a;
    --card-white: #ffffff;
    --ink: #111111;
    --brand-blue: #1a3cf0;
    --line-blue: #2f5be8;
    --grad-orange: #ff9a3c;
    --grad-red: #ff3d4a;
    --grad-pink: #e6446e;
    --grad-violet: #8a5be6;
    --grad-cyan: #22e6f0;
    --text-light: #ffffff;
  }
  * { margin: 0; padding: 0; box-sizing: border-box; }
  html, body { width: 1200px; height: 960px; overflow: hidden; }
  body {
    background: var(--backdrop);
    font-family: "Poppins", sans-serif;
    position: relative;
  }
  .card {
    position: absolute;
    left: 250px;
    width: 700px;
    height: 400px;
    border-radius: 4px;
    box-shadow: 0 10px 30px rgba(0,0,0,0.25);
    overflow: hidden;
  }
  /* Product side */
  .card--product {
    top: 50px;
    background: var(--card-white);
  }
  .product-lockup {
    position: absolute;
    left: 0; right: 0; top: 120px;
    display: flex;
    align-items: center;
    justify-content: center;
    gap: 22px;
  }
  .product-name {
    font-size: 54px;
    font-weight: 600;
    color: var(--brand-blue);
    letter-spacing: -0.5px;
  }
  .lockup-divider {
    width: 1.5px;
    height: 56px;
    background: var(--brand-blue);
  }
  .org-name {
    display: flex;
    flex-direction: column;
    line-height: 1;
  }
  .org-name__main {
    font-size: 30px;
    font-weight: 700;
    color: var(--ink);
    letter-spacing: 3px;
  }
  .org-name__sub {
    margin-top: 6px;
    font-size: 14px;
    font-weight: 400;
    color: var(--ink);
    letter-spacing: 9px;
  }
  .product-tagline {
    position: absolute;
    left: 0; right: 0; top: 215px;
    text-align: center;
    font-size: 17px;
    font-weight: 600;
    color: var(--ink);
  }
  .product-web {
    position: absolute;
    left: 40px; right: 40px; top: 252px;
    height: 30px;
  }
  .product-web svg { position: absolute; inset: 0; }
  .product-web__url {
    position: absolute;
    left: 0; right: 0; top: 2px;
    text-align: center;
    font-size: 17px;
    font-weight: 500;
    color: var(--line-blue);
  }
  .product-edge {
    position: absolute;
    left: 0; right: 0; bottom: 0;
    height: 5px;
    background: linear-gradient(90deg, var(--grad-red), var(--grad-violet));
  }
  /* Contact side */
  .card--contact {
    top: 510px;
    background: linear-gradient(115deg, var(--grad-orange) 0%, var(--grad-red) 22%, var(--grad-pink) 48%, var(--grad-violet) 70%, var(--grad-cyan) 100%);
    color: var(--text-light);
  }
  .contact-brand {
    position: absolute;
    left: 60px; top: 70px;
    display: flex;
    align-items: center;
    gap: 14px;
  }
  .contact-brand__dot {
    width: 22px; height: 22px;
    border-radius: 50%;
    background: var(--text-light);
  }
  .contact-brand__name {
    display: flex;
    flex-direction: column;
    line-height: 1;
  }
  .contact-brand__main {
    font-size: 40px;
    font-weight: 700;
    letter-spacing: 4px;
  }
  .contact-brand__sub {
    margin-top: 8px;
    font-size: 17px;
    font-weight: 400;
    letter-spacing: 12px;
  }
  .contact-person {
    position: absolute;
    left: 60px; top: 205px;
  }
  .contact-person__name {
    font-size: 30px;
    font-weight: 600;
    line-height: 1.1;
  }
  .contact-person__title {
    font-size: 19px;
    font-weight: 500;
  }
  .contact-list {
    list-style: none;
    margin-top: 16px;
  }
  .contact-list li {
    display: flex;
    align-items: center;
    gap: 10px;
    font-size: 18px;
    font-weight: 400;
    line-height: 1.6;
  }
  .contact-list svg { width: 16px; height: 16px; flex: none; }
</style>
</head>
<body>

  <section class="card card--product" aria-label="Product side">
    <div class="product-lockup">
      <span class="product-name">Glimworld</span>
      <span class="lockup-divider"></span>
      <span class="org-name">
        <span class="org-name__main">BRIGHTLOOM</span>
        <span class="org-name__sub">LANGUAGE</span>
      </span>
    </div>
    <p class="product-tagline">Culturally Immersive Language Learning Games</p>
    <div class="product-web">
      <svg viewBox="0 0 620 30" preserveAspectRatio="none" aria-hidden="true">
        <defs>
          <linearGradient id="web-line-left" x1="0" x2="1">
            <stop offset="0" stop-color="#2f5be8" stop-opacity="0"/>
            <stop offset="1" stop-color="#2f5be8"/>
          </linearGradient>
          <linearGradient id="web-line-right" x1="0" x2="1">
            <stop offset="0" stop-color="#2f5be8"/>
            <stop offset="1" stop-color="#2f5be8" stop-opacity="0"/>
          </linearGradient>
        </defs>
        <line x1="0" y1="15" x2="160" y2="15" stroke="url(#web-line-left)" stroke-width="1.5"/>
        <circle cx="166" cy="15" r="5" fill="none" stroke="#2f5be8" stroke-width="1.8"/>
        <circle cx="454" cy="15" r="5" fill="none" stroke="#2f5be8" stroke-width="1.8"/>
        <line x1="460" y1="15" x2="620" y2="15" stroke="url(#web-line-right)" stroke-width="1.5"/>
      </svg>
      <p class="product-web__url">www.glimworld-play.com</p>
    </div>
    <div class="product-edge"></div>
  </section>

  <section class="card card--contact" aria-label="Contact side">
    <div class="contact-brand">
      <span class="contact-brand__dot"></span>
      <span class="contact-brand__name">
        <span class="contact-brand__main">BRIGHTLOOM</span>
        <span class="contact-brand__sub">LANGUAGE</span>
      </span>
    </div>
    <div class="contact-person">
      <p class="contact-person__name">Perry Dunmore</p>
      <p class="contact-person__title">Founder &amp; CEO</p>
      <ul class="contact-list">
        <li>
          <svg viewBox="0 0 24 24" aria-hidden="true"><path fill="#fff" d="M6.6 10.8a15.1 15.1 0 0 0 6.6 6.6l2.2-2.2a1 1 0 0 1 1-.25 11.4 11.4 0 0 0 3.6.57 1 1 0 0 1 1 1V20a1 1 0 0 1-1 1A17 17 0 0 1 3 4a1 1 0 0 1 1-1h3.5a1 1 0 0 1 1 1c0 1.25.2 2.45.57 3.57a1 1 0 0 1-.25 1z"/></svg>
          (555)-014-2286
        </li>
        <li>
          <svg viewBox="0 0 24 24" aria-hidden="true"><path fill="#fff" d="M2 5h20v14H2z"/><path fill="none" stroke="#e6446e" stroke-width="1.6" d="M2.5 5.5 12 13l9.5-7.5"/></svg>
          pdunmore@quillpost-mail.net
        </li>
      </ul>
    </div>
  </section>

</body>
</html>
```